Business Cards

I am a landscape designer and I am hired to do over the top landscapes!
I pay attention to detail and do everything from growing my own orchids and Fruits and Vegetables.
I build ponds water features. I do Landscape Lighting and Specialize in Drip Irrigation for New Landscapes.
I am looking for something with a picture of one of my landscapes and pictures of Orchids on the back so I can work on growing my Orchid business.
I like the plastic cards.
I like Saturation
I like color and I want something that really sticks out!
I will attach a few pics!
Thanks
Corey
A Verdant Terrace LLC
Corey Halvorsen
Rare Blooms & Garden Growing
Outdoor Living Made Easy
561-555-0147
Averdantterrace@mailbrook.net
Coral Harbor FL

Target Market(s)

I work for Wealthy Clients who want unique designs and enjoy rare plants.
I am the goto guy for tropical and rare plants
Cool Designs
Orchids
Interior Decorating
Exterior Lighting
Organic Farming
People who appreciate plants

Industry/Entity Type

Landscape

Font styles to use
Decorative

Requirements
Must have
• COLOR COLOR COLOR
Saturation
Sleek and Clean
Should not have
• tacky

```html
<!DOCTYPE html>
<html lang="en">
<head>
<meta charset="utf-8">
<title>A Verdant Terrace LLC — Business Cards</title>
<link rel="stylesheet" href="https://fonts.googleapis.com/css2?family=Bebas+Neue&display=swap">
<style>
  :root {
    --page-bg: #e9e4dc;
    --leaf-dark: #0f3d12;
    --leaf-mid: #2f8a2a;
    --leaf-light: #7fcf52;
    --orchid: #d62ea8;
    --orchid-deep: #8a1466;
    --sun: #f3e84a;
    --foliage: #3fae3a;
    --sky: #6fc8e8;
    --white: #ffffff;
    --name-green: #7dc142;
    --band: rgba(20, 10, 30, 0.62);
  }
  * { margin: 0; padding: 0; box-sizing: border-box; }
  html, body {
    width: 1200px; height: 900px; overflow: hidden;
    background: var(--page-bg);
    font-family: "Bebas Neue", "Oswald", sans-serif;
  }
  .canvas { position: relative; width: 1200px; height: 900px; }

  .card {
    position: absolute; left: 275px; width: 650px; height: 370px;
    overflow: hidden;
    box-shadow: 0 6px 16px rgba(0,0,0,0.25);
  }
  .card--front { top: 45px; }
  .card--back { top: 481px; }

  .photo { position: absolute; inset: 0; }
  .photo--leaves {
    background:
      radial-gradient(ellipse at 25% 30%, var(--leaf-light) 0%, transparent 45%),
      radial-gradient(ellipse at 70% 75%, var(--leaf-mid) 0%, transparent 55%),
      linear-gradient(135deg, var(--leaf-mid) 0%, var(--leaf-dark) 60%, #1b5a1a 100%);
  }
  .photo--orchids {
    background:
      radial-gradient(ellipse at 35% 60%, var(--orchid) 0%, var(--orchid-deep) 28%, transparent 48%),
      radial-gradient(ellipse at 70% 10%, var(--orchid) 0%, transparent 30%),
      radial-gradient(ellipse at 8% 25%, var(--sun) 0%, transparent 40%),
      radial-gradient(ellipse at 90% 40%, var(--sky) 0%, transparent 40%),
      linear-gradient(160deg, var(--foliage) 0%, #b5d94a 45%, #2c7a3a 100%);
  }

  .brand {
    position: absolute; right: 24px; top: 28px;
    text-align: right; color: var(--white);
    font-weight: 400;
    font-size: 118px; line-height: 96px; letter-spacing: 1px;
  }
  .brand__line { display: block; }
  .brand__tail { display: flex; justify-content: flex-end; align-items: flex-end; gap: 12px; }
  .tagline {
    font-size: 25px; line-height: 28px; letter-spacing: 1.5px;
    text-align: right; padding-bottom: 22px;
  }

  .band {
    position: absolute; right: 0; left: 255px;
    background: var(--band);
    text-align: right; padding-right: 28px;
    font-weight: 400;
  }
  .band--name {
    top: 67px; height: 60px;
    color: var(--name-green); font-size: 56px; line-height: 64px; letter-spacing: 1px;
  }
  .band--contact {
    top: 222px; height: 97px;
    color: var(--white); font-size: 27px; line-height: 28px; letter-spacing: 1px;
    padding-top: 6px; font-style: normal;
  }
  .contact__item { display: block; }
</style>
</head>
<body>
<main class="canvas">
  <section class="card card--front">
    <div class="photo photo--leaves" role="img" aria-label="Close-up photo of lush striped tropical leaves"></div>
    <h1 class="brand">
      <span class="brand__line">A Verdant</span>
      <span class="brand__line">Terrace</span>
      <span class="brand__tail">
        <span class="tagline">Rare Blooms &amp; Garden Growing<br>Outdoor Living Made Easy</span>
        <span>LLC</span>
      </span>
    </h1>
  </section>

  <section class="card card--back">
    <div class="photo photo--orchids" role="img" aria-label="Vivid photo of magenta orchid blooms against sunny foliage"></div>
    <h2 class="band band--name">Corey Halvorsen</h2>
    <address class="band band--contact">
      <span class="contact__item">561-555-0147</span>
      <span class="contact__item">Averdantterrace@mailbrook.net</span>
      <span class="contact__item">Coral Harbor FL</span>
    </address>
  </section>
</main>
</body>
</html>
```